Upmarket Dessert Lounge needs a Business Card Design

We are an upmarket dessert lounge needing a business card to match our image.

We want something that is simple yet beautiful, feminine, classy, sophisticated and elegant. We want it to stand out and don't mind if it is bold.

The design should include our logo and colours of red or maroon with gold highlights. We don't mind if black is used.

Marlow & Quince

Target Market(s)

For those who like to indulge or treat themselves and give in to their temptations on good quality desserts.

Industry/Entity Type

Business

Requirements
Must have
• Must include our logo and our name

Marlow & Quince

M & Q

```html
<!DOCTYPE html>
<html lang="en">
<head>
<meta charset="utf-8">
<title>Marlow &amp; Quince — Business Card</title>
<link href="https://fonts.googleapis.com/css2?family=Open+Sans:wght@400;600;700&display=swap" rel="stylesheet">
<style>
  :root {
    --maroon: #7a1315;
    --cream: #fdd49a;
    --paper: #ffffff;
    --ink: #333333;
    --backdrop: #e4e4e4;
  }
  * { margin: 0; padding: 0; box-sizing: border-box; }
  html, body { width: 956px; height: 1200px; overflow: hidden; }
  body {
    position: relative;
    background: var(--backdrop);
    font-family: "Open Sans", Arial, sans-serif;
    color: var(--ink);
  }
  .card {
    position: absolute;
    width: 798px;
    height: 455px;
    background: var(--paper);
    border-radius: 30px;
    overflow: hidden;
    box-shadow: 0 6px 14px rgba(0,0,0,0.25);
  }
  .card--front { left: 70px; top: 85px; }
  .card--back { left: 73px; top: 632px; }
  .swoosh { position: absolute; inset: 0; }
  .brand {
    position: absolute;
    display: flex;
    align-items: center;
    justify-content: center;
    color: var(--maroon);
    font-weight: 600;
    white-space: nowrap;
  }
  .brand--monogram { left: 40px; top: 140px; width: 300px; font-size: 64px; }
  .brand--wordmark { left: 0; top: 195px; width: 798px; font-size: 44px; letter-spacing: 1px; }
  .identity { position: absolute; left: 400px; top: 70px; }
  .identity__name { font-size: 22px; font-weight: 700; line-height: 26px; }
  .identity__role { font-size: 22px; font-weight: 400; line-height: 26px; letter-spacing: 0.5px; }
  .contacts { position: absolute; left: 403px; top: 144px; list-style: none; font-size: 19px; }
  .contacts li { line-height: 30px; }
  .contacts li.gap { margin-top: 7px; }
  .contacts b { font-weight: 700; }
  .address { position: absolute; left: 72px; top: 406px; font-size: 19px; }
</style>
</head>
<body>
  <section class="card card--front">
    <svg class="swoosh" width="798" height="455" viewBox="0 0 798 455">
      <path d="M733,170 C738,300 640,410 435,455 L628,455 C690,405 737,320 740,200 C739,190 736,180 733,170 Z" fill="var(--cream)"/>
      <path d="M636,0 C705,45 742,110 740,200 C737,320 690,405 628,455 L798,455 L798,0 Z" fill="var(--maroon)"/>
      <path d="M636,0 C705,45 742,110 740,200 C737,320 690,405 628,455" fill="none" stroke="var(--paper)" stroke-width="5"/>
    </svg>
    <div class="brand brand--monogram"><span>M &amp; Q</span></div>
    <div class="identity">
      <div class="identity__name">Your Name</div>
      <div class="identity__role">Designation</div>
    </div>
    <ul class="contacts">
      <li><b>p</b> : 123-456-7890</li>
      <li><b>c</b> : 123-456-7890</li>
      <li><b>f</b> : 123-456-7890</li>
      <li class="gap"><b>e</b> : name@yourwebsite.com</li>
      <li><b>w</b> : www.marlow&amp;quince.com</li>
    </ul>
    <p class="address">0000, Street Name, City Name, Country Code.</p>
  </section>

  <section class="card card--back">
    <div class="brand brand--wordmark"><span>MARLOW &amp; QUINCE</span></div>
  </section>
</body>
</html>
```